Business Cards Design for the electrical wholesaler: clean bold dynamic :)

We need a business card design that would follow our latest brand guidelines. As an electrical wholesaler we want to bring a fresh look and feel into the industry. The design should be clean bold and dynamic. It should come alive with the renewed energy of our green colour. Our grey colour should keep things balanced and complement the notion of maturity and responsibility. We employ Lato as a corporate font however are not bound by this font and we’re open to interpretation here.

Target Market(s)

Electrical contractors

Industry/Entity Type

Business

Contact Information for Business Card

Logo
Name & Surname: Halyna Dorosh
Job Title: Director of Marketing
Email: halya.dorosh@quillmail.example
Cell phone: XXX.XXX.XXXX
Address: 20517 - 87 Ave. Edmonton, AB, Canada. T6K 4N8
Business Phone: 780.555.0184
Website: www.brovix.example

Font styles to use
Other font styles liked:
• Lato

Requirements
Must have
• Logo & website
Nice to have
• Brand elements - some of them you may find in the attached Brand Guidelines (e.g. three lines on the background signifying "W")

```html
<!DOCTYPE html>
<html lang="en">
<head>
<meta charset="utf-8">
<title>Brovix Business Cards</title>
<link rel="stylesheet" href="https://fonts.googleapis.com/css2?family=Work+Sans:wght@400;500;600&display=swap">
<style>
  :root {
    --backdrop: #3a322f;
    --card: #1c1c1c;
    --card-deep: #141414;
    --green: #7cc242;
    --white: #f4f4f4;
    --emboss: #4a4a4a;
  }
  * { box-sizing: border-box; margin: 0; padding: 0; }
  html, body { width: 1200px; height: 715px; overflow: hidden; }
  body {
    background: var(--backdrop);
    font-family: "Work Sans", Arial, sans-serif;
    position: relative;
  }
  .card {
    position: absolute;
    width: 500px;
    height: 286px;
    background: var(--card);
    border-radius: 4px;
    box-shadow: 0 18px 30px rgba(0,0,0,.45);
  }
  .card--front {
    left: 60px; top: 214px;
    background: var(--card-deep);
    border-bottom: 6px solid var(--green);
  }
  .card--back { left: 640px; top: 214px; }

  .front-name {
    position: absolute;
    left: 0; right: 0; top: 100px;
    text-align: center;
    font-size: 64px;
    font-weight: 600;
    color: var(--emboss);
    letter-spacing: 1px;
  }

  .back-brand {
    position: absolute;
    left: 36px; top: 112px;
    display: flex; align-items: center; gap: 12px;
  }
  .brand-square { width: 22px; height: 22px; background: var(--green); }
  .brand-name {
    font-size: 42px; font-weight: 600; color: var(--white);
  }
  .divider {
    position: absolute;
    left: 262px; top: 54px;
    width: 2px; height: 178px;
    background: var(--green);
  }
  .contact {
    position: absolute;
    left: 284px; top: 62px;
    color: var(--white);
    font-size: 13px;
    line-height: 1.45;
  }
  .contact-name { color: var(--green); font-size: 21px; font-weight: 600; line-height: 1.1; }
  .contact-role { font-size: 14px; margin-bottom: 8px; }
  .contact-line { display: flex; align-items: center; gap: 7px; }
  .contact-line svg { width: 10px; height: 10px; flex: none; }
  .contact-line--plain { padding-left: 17px; }
</style>
</head>
<body>
  <section class="card card--front" aria-label="Card front">
    <div class="front-name">Brovix</div>
  </section>

  <section class="card card--back" aria-label="Card back">
    <div class="back-brand">
      <span class="brand-square"></span>
      <span class="brand-name">Brovix</span>
    </div>
    <div class="divider"></div>
    <div class="contact">
      <div class="contact-name">Halyna Dorosh</div>
      <div class="contact-role">Founder</div>
      <div class="contact-line contact-line--plain">20517 87ave</div>
      <div class="contact-line contact-line--plain">T6K4N8 Edmonton, Alberta</div>
      <div class="contact-line">
        <svg viewBox="0 0 10 10"><path d="M2 0.5 L4 3 L3 4 Q4.5 6 6 7 L7 6 L9.5 8 L8 9.5 Q3 8.5 0.5 2 Z" fill="var(--green)"/></svg>
        780.555.0184
      </div>
      <div class="contact-line">
        <svg viewBox="0 0 10 10"><rect x="0.5" y="2" width="9" height="6.5" fill="none" stroke="var(--green)" stroke-width="1"/><path d="M0.5 2 L5 5.5 L9.5 2" fill="none" stroke="var(--green)" stroke-width="1"/></svg>
        hello@brovix.example
      </div>
      <div class="contact-line">
        <svg viewBox="0 0 10 10"><circle cx="5" cy="5" r="4.3" fill="none" stroke="var(--green)" stroke-width="1"/><ellipse cx="5" cy="5" rx="1.8" ry="4.3" fill="none" stroke="var(--green)" stroke-width="0.8"/><path d="M0.7 5 H9.3" stroke="var(--green)" stroke-width="0.8"/></svg>
        www.brovix.example
      </div>
    </div>
  </section>
</body>
</html>
```